Tellmora Corporate Stationery

Look for design of all new corporate stationery for an existing insurance broking business that is going through a redesign and move from older partners to younger family members. New Logo is attached. Company is Brisbane based.
Colours in the Logo is Hex #43bed8 and website features a lot of hex #17b8d8. Website front page "A plan to protect you" - headline. "Professional and Individual advice to protect your greatest assets" - tagline.

Stationery required: Business Cards, Letter head, Thank-you cards, Birthday cards, Presentation folders, With Compliment slips and a powerpoint template. We also would like to send a card to all customers with the something along of the lines of "something new".

Target Market(s)

Customers of Insurance business looking at superannuation, life and income protection insurance, investment advice and wills

Industry/Entity Type

Insurance Broker

Font styles to use
Other font styles liked:
• same as logo

Requirements
Must have
• The above designs for new stationery for the new business including:
• Business Cards, Letter head, Thank-you cards, Birthday cards, Presentation folders, With Compliment slips and a powerpoint template. We also would like to send a card to all customers with the something along of the lines of "something new".
Nice to have
• It is a new look - long time family business being passed to next generation - big focus on advice for YOU, individual advice etc..

```html
<!DOCTYPE html>
<html lang="en">
<head>
<meta charset="utf-8">
<title>Tellmora Business Card</title>
<link href="https://fonts.googleapis.com/css2?family=Open+Sans:wght@400;600;700&display=swap" rel="stylesheet">
<style>
  :root{
    --brand-cyan:#43bed8;
    --band-cyan:#4cc3dc;
    --ink-grey:#6b6b6b;
    --soft-grey:#a8a8a8;
    --rule-grey:#d9d9d9;
    --card-white:#ffffff;
    --page-bg:#ecebe8;
  }
  *{box-sizing:border-box;margin:0;padding:0}
  html,body{width:1200px;height:950px;overflow:hidden}
  body{background:var(--page-bg);font-family:"Open Sans",Arial,sans-serif;position:relative}
  .card{position:absolute;left:250px;width:700px;height:400px;border-radius:26px;overflow:hidden;
        box-shadow:0 6px 18px rgba(0,0,0,.18)}
  .card-front{top:45px;background:var(--card-white)}
  .card-back{top:505px;background:var(--band-cyan)}

  .front-band{position:absolute;inset:0}
  .band-web{position:absolute;left:400px;top:342px;color:#fff;font-size:17px;letter-spacing:4px;
            transform:rotate(-7deg);transform-origin:left center}

  .brand{position:absolute;left:70px;top:150px;display:flex;align-items:center;gap:16px}
  .brand-dot{width:46px;height:46px;border-radius:50%;background:var(--brand-cyan)}
  .brand-name{font-size:40px;font-weight:700;color:var(--brand-cyan);letter-spacing:1px;text-transform:uppercase}

  .divider{position:absolute;left:372px;top:40px;width:1px;height:230px;background:var(--rule-grey)}

  .contact{position:absolute;left:400px;top:52px;color:var(--ink-grey)}
  .contact-name{font-size:22px;font-weight:600;color:var(--brand-cyan);letter-spacing:.5px}
  .contact-role{font-size:14px;color:var(--soft-grey);margin-bottom:12px}
  .contact-address{font-size:14px;line-height:1.4;margin-bottom:8px}
  .contact-list{list-style:none;font-size:14px;line-height:1.65}
  .contact-list li{display:flex;align-items:center;gap:9px}
  .contact-list svg{width:13px;height:13px;fill:var(--brand-cyan)}

  .back-pattern{position:absolute;inset:0;background:linear-gradient(135deg,#52c7df,#43bed8)}
  .back-mark{position:absolute;left:50%;top:50%;width:52px;height:52px;margin:-26px 0 0 -26px;
             border-radius:50%;background:#fff}
  .back-web{position:absolute;left:40px;bottom:34px;color:#fff;font-size:16px;letter-spacing:4px}
</style>
</head>
<body>

<section class="card card-front">
  <svg class="front-band" viewBox="0 0 700 400" width="700" height="400" aria-hidden="true">
    <path d="M0 372 C230 372 450 352 700 268 L700 280 C450 364 230 384 0 384 Z" fill="#b9b9b9"/>
    <path d="M0 384 C230 384 450 364 700 280 L700 400 L0 400 Z" fill="var(--band-cyan)"/>
  </svg>

  <div class="brand">
    <span class="brand-dot"></span>
    <span class="brand-name">Tellmora</span>
  </div>

  <div class="divider"></div>

  <div class="contact">
    <p class="contact-name">DANIEL HART</p>
    <p class="contact-role">CEO/FOUNDER</p>
    <p class="contact-address">412 Wattle Grove<br>Brisbane QLD 4000</p>
    <ul class="contact-list">
      <li><svg viewBox="0 0 24 24"><path d="M6.6 10.8a15 15 0 0 0 6.6 6.6l2.2-2.2a1 1 0 0 1 1-.25 11.4 11.4 0 0 0 3.6.57 1 1 0 0 1 1 1V20a1 1 0 0 1-1 1A17 17 0 0 1 3 4a1 1 0 0 1 1-1h3.5a1 1 0 0 1 1 1c0 1.25.2 2.45.57 3.57a1 1 0 0 1-.25 1z"/></svg>07 3184 5520</li>
      <li><svg viewBox="0 0 24 24"><path d="M7 1h10a2 2 0 0 1 2 2v18a2 2 0 0 1-2 2H7a2 2 0 0 1-2-2V3a2 2 0 0 1 2-2zm0 3v14h10V4z"/></svg>0412 733 918</li>
      <li><svg viewBox="0 0 24 24"><path d="M6 2h12v6H6zM4 9h16a2 2 0 0 1 2 2v7h-4v4H6v-4H2v-7a2 2 0 0 1 2-2zm4 7v4h8v-4z"/></svg>07 3184 5521</li>
      <li><svg viewBox="0 0 24 24"><path d="M2 5h20v14H2zm2 2v.5l8 5 8-5V7z"/></svg>daniel@tellmora.com</li>
    </ul>
  </div>

  <p class="band-web">www.tellmora.com</p>
</section>

<section class="card card-back">
  <div class="back-pattern" role="img" aria-label="Faint repeating brand pattern in light cyan tones"></div>
  <span class="back-mark"></span>
  <p class="back-web">www.tellmora.com</p>
</section>

</body>
</html>
```